Business Card for beauty technology startup

Design Glimora Business Card for a Beauty, based on the website identity and colors (https://www.glimora-example.com).
Glimora is a beauty tech startup that gathers helpful product info for beauty lovers and consumers (such as availability on stores, price range and product reviews) for makeup products. The card design must be young, colorful but clean, and very modern.

Target Market(s)

woman, 15-35

Industry/Entity Type

Cosmetics

Contact Information for Business Card

Full Name, address, phone

Font styles to use
Other font styles liked:
• Advent Pro

Colors
e34297
86cfc6
ffffff
5c5c5c
e8e8e8
e667a6
b2b2b2

Requirements
Must have
• One full colored side with a creative design and another with card info
• Use Color palette: #95C5C5 and/or #D38AA5
• Use fonts: Advent Pro
• Use website identity: https://www.glimora-example.com
Nice to have
• If needed extra font: Roboto

```html
<!DOCTYPE html>
<html lang="en">
<head>
<meta charset="utf-8">
<title>Glimora Business Card</title>
<link rel="stylesheet" href="https://fonts.googleapis.com/css2?family=Advent+Pro:wght@300;400&family=Roboto:wght@400;500&family=Roboto+Condensed:wght@700&display=swap">
<style>
  :root {
    --stage: #2b2b2b;
    --paper: #f4f4f4;
    --rose: #b77d92;
    --rose-back: #b5808f;
    --rose-light: #c18b9c;
    --ink: #4a4a4a;
    --band-grey: #a9a9a9;
    --white: #ffffff;
  }
  * { box-sizing: border-box; margin: 0; padding: 0; }
  html, body { width: 1200px; height: 960px; overflow: hidden; }
  body { background: var(--stage); position: relative; font-family: "Roboto", Arial, sans-serif; }

  .card { position: absolute; width: 600px; height: 342px; border-radius: 20px; overflow: hidden; }

  /* Front side */
  .card-front { left: 314px; top: 114px; background: var(--paper); }
  .brand { position: absolute; left: 47px; top: 44px; display: flex; align-items: center; gap: 22px; }
  .brand-dot { width: 70px; height: 70px; border: 2px solid var(--rose); border-radius: 50%; }
  .brand-name { font-family: "Advent Pro", sans-serif; font-weight: 300; font-size: 50px; letter-spacing: 5px; color: var(--rose); text-transform: uppercase; line-height: 1; }

  .address { position: absolute; left: 47px; top: 159px; font-size: 14px; line-height: 18px; color: var(--ink); }
  .contacts { position: absolute; left: 47px; top: 205px; list-style: none; font-size: 14px; color: var(--ink); }
  .contacts li { display: flex; align-items: center; height: 20px; gap: 8px; }
  .contacts svg { width: 14px; height: 14px; fill: var(--rose); flex: none; }

  .person { position: absolute; right: 37px; top: 199px; text-align: right; }
  .person-name { font-family: "Roboto Condensed", sans-serif; font-weight: 700; font-size: 21px; color: var(--rose); text-transform: uppercase; line-height: 24px; }
  .person-role { font-family: "Roboto Condensed", sans-serif; font-weight: 700; font-size: 14px; color: var(--ink); text-transform: uppercase; line-height: 18px; }

  .band-grey { position: absolute; left: 0; bottom: 0; width: 100%; height: 16px; background: var(--band-grey); }
  .band-web { position: absolute; left: 332px; bottom: 0; width: 268px; height: 42px; background: var(--rose); border-top-left-radius: 42px 40px; border-left: 2px solid var(--paper); display: flex; align-items: center; justify-content: flex-end; padding-right: 36px; }
  .band-web span { color: var(--white); font-size: 13px; letter-spacing: 1.6px; }

  /* Back side */
  .card-back { left: 311px; top: 473px; }
  .back-field { position: absolute; inset: 0; background: linear-gradient(135deg, var(--rose-light), var(--rose-back)); }
  .back-mark { position: absolute; right: 42px; top: 206px; display: flex; flex-direction: column; align-items: flex-end; gap: 14px; }
  .back-brand { display: flex; align-items: center; gap: 12px; }
  .back-dot { width: 60px; height: 60px; border: 3px solid var(--white); border-radius: 50%; }
  .back-name { font-family: "Advent Pro", sans-serif; font-weight: 400; font-size: 30px; color: var(--white); letter-spacing: 2px; }
  .back-web { color: var(--white); font-size: 13px; letter-spacing: 1px; }
</style>
</head>
<body>
  <section class="card card-front" aria-label="Front of business card">
    <div class="brand">
      <div class="brand-dot"></div>
      <span class="brand-name">Glimora</span>
    </div>

    <p class="address">214 Larkspur Court<br>Juneau, Alaska 99801</p>

    <ul class="contacts">
      <li><svg viewBox="0 0 16 16"><path d="M3.6 1.2l2.3 2.6-1.2 1.9c.9 2 2.5 3.6 4.6 4.6l1.9-1.2 2.6 2.3-1.3 2.8C7.4 14 2 8.6 1 3.8z"/></svg>555 214 7390</li>
      <li><svg viewBox="0 0 16 16"><path d="M4 1h8v14H4zM5.5 2.5v9h5v-9zM7 12.8h2v1H7z" fill-rule="evenodd"/></svg>555 308 1642</li>
      <li><svg viewBox="0 0 16 16"><path d="M4 1h8v4H4zM1 6h14v6h-2v-2H3v2H1zM4 11h8v4H4z"/></svg>555 762 4105</li>
      <li><svg viewBox="0 0 16 16"><path d="M1 4h14v1L8 9 1 5zM1 6.5l7 4 7-4V13H1z"/></svg>info@glimora-example.com</li>
    </ul>

    <div class="person">
      <p class="person-name">Mara Lindqvist</p>
      <p class="person-role">CEO/Founder</p>
    </div>

    <div class="band-grey"></div>
    <div class="band-web"><span>www.glimora-example.com</span></div>
  </section>

  <section class="card card-back" aria-label="Back of business card">
    <div class="back-field" role="img" aria-label="Rose-toned background with a repeating brand motif pattern"></div>
    <div class="back-mark">
      <div class="back-brand">
        <span class="back-name">Glimora</span>
        <div class="back-dot"></div>
      </div>
      <span class="back-web">www.glimora-example.com</span>
    </div>
  </section>
</body>
</html>
```